Website redesign for a Medical Office

We are a physician office in need of a website redesign and a face-lift.
1.Website must work on all platforms including mobile phones and tablets.
2.Website will also include and interactive CONTACT US form and payment gateway for office to collect payment from patients online.
3.Website should have the ability for us to easily edit content without resorting to the services of an IT person.
4. Website content will be collected from the present website www.sunbrookkids.com.
- The type of upgrade we are looking for is more of a corrective work. The major problems with the current website are:
1. Contact Us form not working correctly
2. Credit card/monetrix gateway not working as intended
3. Needing better images/pictures to correctly reflect our business.
4. General enhancement to the overall feel and outlook of the current website.

5. Once a design is selected, website MUST be up and live within TWO WEEKS. The designer able to make this work within the time-frame will get an extra bonus.

Target Market(s)

General public; including patients and their parents.

Industry/Entity Type

Healthcare

Coding

Coded - Design and coding required

Number of Pages Required

5+ page

Font styles to use
Sans Serif

Colors
0492cd
33a6d7
85cae6
cee9f5
cedeed
acd036
cadf82
00a990
f04a50

Requirements
Must have
• 1. Ability for the website to work on all platforms including mobile phones and tablets.
• 2. Include an interactive CONTACT US form
• 3. A payment gateway for office to collect payment from patients online using credit cards and Monetrix.
• 4. Website should have the ability for us to easily edit content without resorting to the services of an IT person.
• 5. Once a design is selected, website MUST be up and live within TWO WEEKS.
• 6. Social network buttons.
• 7. A Vorlund map with office location or geo-tag and directions to office.
Nice to have
• Nice theme, children friendly with a flashy home page and inside pages.
• Attractive design with wow factor

```html
<!DOCTYPE html>
<html lang="en">
<head>
<meta charset="utf-8">
<title>Sunbrook Pediatrics</title>
<link rel="stylesheet" href="https://fonts.googleapis.com/css2?family=Open+Sans:wght@400;600;700&display=swap">
<style>
:root{
  --blue:#0492cd;--blue2:#33a6d7;--blue3:#85cae6;--blue4:#cee9f5;--steel:#cedeed;
  --green:#acd036;--green2:#cadf82;--teal:#00a990;--red:#f04a50;
  --ink:#444;--muted:#777;--footer:#2a2a2a;
}
*{box-sizing:border-box;margin:0;padding:0}
html,body{width:1200px;height:2927px;overflow:hidden}
body{position:relative;font-family:"Open Sans",sans-serif;color:var(--ink);
  background:linear-gradient(#ffffff 0,#f4f8f4 40%,#eef6ea 80%,#c8e39a 92%,#9bcb4f 100%)}
.abs{position:absolute}
.scenery-left{left:0;top:90px;width:133px;height:2700px;background:linear-gradient(#e3f1d0,#f4f8f1 30%,#f4f8f1 75%,#b7da74);opacity:.8}
.scenery-right{right:0;top:90px;width:131px;height:2700px;background:linear-gradient(#e3f1d0,#f4f8f1 30%,#f4f8f1 75%,#b7da74);opacity:.8}
/* header */
.brand{left:133px;top:30px;display:flex;align-items:center;gap:12px;color:var(--blue);font-weight:700;line-height:1.05;font-size:27px}
.brand .mark{width:48px;height:48px;background:var(--blue)}
.hours,.contact{top:40px;text-align:right;font-size:14px;color:var(--muted);line-height:1.5}
.hours{left:690px;width:200px}
.contact{left:900px;width:169px}
.hours b,.contact b{display:block;color:var(--red);font-weight:400;font-size:16px}
/* nav */
.nav{left:133px;top:113px;width:936px;height:43px;display:flex;gap:4px;list-style:none}
.nav li{flex:auto;background:var(--green);color:#fff;font-size:11.5px;font-weight:600;text-align:center;line-height:43px;border-radius:3px 3px 0 0;letter-spacing:.3px}
.nav li.active{background:var(--red);flex:0 0 96px}
/* panel */
.panel{left:133px;top:156px;width:936px;height:2604px;background:#fff;box-shadow:0 0 6px rgba(0,0,0,.12)}
/* hero */
.hero{left:152px;top:176px;width:896px;height:458px;background:linear-gradient(100deg,#e9e6cf 0,#f2efe2 40%,#dfe6d8 70%,#c9c2b4 100%)}
.hero-arrow{top:390px;width:34px;height:34px;border-radius:50%;background:rgba(120,120,120,.5);color:#fff;font-size:18px;text-align:center;line-height:34px}
.vision{left:600px;top:275px;width:380px;text-align:right}
.vision h2{color:var(--red);font-size:31px;font-weight:600;line-height:1.1;margin-bottom:8px}
.vision p{font-size:12.5px;line-height:1.55;color:#333}
.btn{display:inline-block;background:var(--red);color:#fff;font-size:12px;padding:9px 18px;border-radius:3px}
.vision .btn{margin-top:14px}
/* welcome */
.welcome{left:170px;top:686px;width:860px;text-align:center}
.welcome h1{color:var(--blue);font-size:34px;font-weight:700;margin-bottom:18px}
.welcome p{font-size:12.5px;line-height:1.7;color:#333}
.welcome .btn{background:var(--blue);margin-top:18px}
/* services */
.services{left:152px;top:933px;width:896px;height:337px;background:linear-gradient(#ede8e0,#f6f3ee 60%,#ebe6dd);display:flex;gap:12px;padding:70px 12px 0}
.card{flex:1;height:210px;background:#fff;box-shadow:0 1px 4px rgba(0,0,0,.15);text-align:center;padding:26px 14px 0}
.card svg{height:46px;width:56px}
.card h3{color:var(--red);font-size:15px;font-weight:400;margin:12px 0 10px}
.card p{font-size:9.5px;line-height:1.6;color:var(--muted)}
/* archives */
.archives{left:152px;top:1335px;width:896px;text-align:center}
.archives h2{color:var(--green);font-size:31px;font-weight:700;margin-bottom:10px}
.archives>p{font-size:12.5px;line-height:1.6;color:#333}
.post{width:436px;height:126px}
.post .thumb{left:0;top:0;width:160px;height:126px}
.post .body{left:172px;top:-4px;width:264px}
.post h4{font-size:13.5px;font-weight:400;color:#222}
.post .meta{font-size:9.5px;color:var(--muted);margin:4px 0 8px}
.post p{font-size:10px;line-height:1.6;color:var(--muted)}
.post .more{font-size:9px;color:var(--green);margin-top:12px;font-weight:600}
/* health center */
.health{left:152px;top:1844px;width:896px;height:335px;background:radial-gradient(ellipse at 50% 50%,#f4f4f4,#dedede 60%,#cfcfcf);text-align:center;padding-top:92px}
.health h2{color:var(--red);font-size:31px;font-weight:600;margin-bottom:14px}
.tags{display:flex;flex-wrap:wrap;justify-content:center;gap:16px 12px;width:820px;margin:0 auto}
.tag{background:var(--red);color:#fff;font-size:14.5px;padding:9px 17px;border-radius:2px}
/* contact */
.contact-sec{left:152px;top:2249px;width:896px;text-align:center}
.contact-sec h2{color:var(--green);font-size:31px;font-weight:700}
.about{left:164px;top:2324px;width:450px}
.about h3,.info h3{font-size:19px;font-weight:400;color:#222;margin-bottom:14px}
.about p{font-size:11px;line-height:1.75;color:#444;margin-bottom:12px}
.info{left:164px;top:2496px;width:450px}
.info li{list-style:none;font-size:12.5px;line-height:2.2;color:#333;display:flex;align-items:center;gap:12px}
.info svg{width:12px;height:12px;fill:#333}
.social{left:164px;top:2640px;display:flex;gap:10px;align-items:center}
.soc{font-size:12px;font-weight:600;color:var(--blue);display:flex;align-items:center;gap:5px}
.soc i{width:14px;height:14px;background:var(--blue);display:block}
.pay{font-size:11px;font-weight:600;color:#555;border:1px solid #ccc;padding:3px 6px}
.map{left:644px;top:2335px;width:388px;height:338px;background:linear-gradient(135deg,#eef0ee,#e4e8e2 50%,#f1ede0);border:1px solid #ddd}
/* footer */
.footer{left:133px;top:2796px;width:936px;height:131px;background:var(--footer);color:#bbb;font-size:10.5px}
.footer nav{left:18px;top:40px}
.footer .copy{left:18px;top:68px}
.footer .flogo{right:20px;top:42px;display:flex;align-items:center;gap:8px;color:#999;font-weight:700;font-size:15px;line-height:1.05}
.flogo i{width:34px;height:34px;background:#999;display:block}
</style>
</head>
<body>
<div class="abs scenery-left" role="img" aria-label="Soft illustrated park scenery with trees and grass"></div>
<div class="abs scenery-right" role="img" aria-label="Soft illustrated park scenery with trees and a fence"></div>

<header>
  <div class="abs brand"><span class="mark"></span><span>SUNBROOK<br>PEDIATRICS</span></div>
  <div class="abs hours">Opening Hours<b>M-F 8:30AM - 5:30PM</b></div>
  <div class="abs contact">Contact<b>(555) 014-2739</b></div>
</header>

<ul class="abs nav">
  <li class="active">HOME</li><li>ABOUT US</li><li>OUR SERVICES</li><li>SUNBROOK HEALTH CENTER</li><li>FORMS</li><li>LATEST NEWS</li><li>CONTACT US</li>
</ul>

<div class="abs panel"></div>

<section>
  <div class="abs hero" role="img" aria-label="Photo of two young girls playing with pillows in a bright bedroom"></div>
  <div class="abs hero-arrow" style="left:133px">&#8249;</div>
  <div class="abs hero-arrow" style="left:1032px">&#8250;</div>
  <div class="abs vision">
    <h2>OUR VISION</h2>
    <p>To raise a generation of children who are strong and healthy.<br>To create an atmosphere that is friendly and conducive to all<br>families— regardless of age, race, or gender.</p>
    <span class="btn">Read more</span>
  </div>
</section>

<section class="abs welcome">
  <h1>Welcome to Sunbrook Pediatrics!</h1>
  <p>Sunbrook Pediatrics is a modern pediatric practice dedicated to the health and wellness of children. It is the pediatrician office of choice in Linwood,<br>Georgia. At Sunbrook Pediatrics, you will find a pediatrician and an environment that is warm and compassionate. All of our staff members<br>are knowledgeable, caring, efficient, and ready to serve you.</p>
  <span class="btn">Read more</span>
</section>

<section class="abs services">
  <div class="card">
    <svg viewBox="0 0 56 46"><path d="M28 44 6 22a12 12 0 0 1 22-14 12 12 0 0 1 22 14z" fill="#e8433a"/><path d="M8 24h12l4-8 5 14 4-10 3 4h12" stroke="#fff" stroke-width="2.5" fill="none"/></svg>
    <h3>General Medical Care</h3>
    <p>Routine office visits for common ailments, Immunizations, ADHD Evaluation and Treatment, Asthma Care, Allergy Testing, Same-day sick appointments.</p>
  </div>
  <div class="card">
    <svg viewBox="0 0 56 46"><circle cx="28" cy="23" r="20" fill="#f5c08a"/></svg>
    <h3>Newborn Care</h3>
    <p>Evaluation of the newborn, Infant circumcision</p>
  </div>
  <div class="card">
    <svg viewBox="0 0 56 46"><path d="M20 3v14a8 8 0 0 0 16 0V3" stroke="#2aa9a0" stroke-width="3" fill="none"/><path d="M28 25v8a8 8 0 0 0 16 0v-6" stroke="#2aa9a0" stroke-width="3" fill="none"/><circle cx="44" cy="24" r="4" fill="#e8433a"/></svg>
    <h3>Physical Examinations</h3>
    <p>Routine Annual Physicals, Sports Physicals, School and College Physicals, Camp Physicals</p>
  </div>
  <div class="card">
    <svg viewBox="0 0 56 46"><rect x="2" y="10" width="34" height="26" fill="#eee" stroke="#999"/><path d="M36 18h10l8 9v9H36z" fill="#ddd" stroke="#999"/><rect x="2" y="26" width="52" height="4" fill="#e8433a"/><path d="M16 14h6v5h5v6h-5v0h-6v0h-5v-6h5z" fill="#e8433a"/><circle cx="14" cy="38" r="5" fill="#333"/><circle cx="44" cy="38" r="5" fill="#333"/></svg>
    <h3>Emergency Care</h3>
    <p>Management of simple injuries, Strains and sprains, Lacerations, Drainage of simple cysts and abscesses, Removal of foreign bodies and splints</p>
  </div>
</section>

<section class="abs archives">
  <h2>From Our Medical Archives</h2>
  <p>There is nothing more joyful to us as loving parents than that moment when we hold our precious little baby, or babies, in our arms after birth. We should<br>acknowledge them as gifts from God and count ourselves blessed to have them.</p>
</section>

<article class="abs post" style="left:152px;top:1471px">
  <div class="abs thumb" role="img" aria-label="Book cover with a baby on a green background" style="background:linear-gradient(135deg,#c9b36a,#9fbf7a 60%,#7aa860)"></div>
  <div class="abs body"><h4>Common Childhood Illnesses</h4><div class="meta">14 December, 2016, by Admin</div><p>As they grow and develop, children come in contact with and may sometimes suffer from a variety of common illnesses...</p><div class="more">+ MORE</div></div>
</article>
<article class="abs post" style="left:620px;top:1471px">
  <div class="abs thumb" role="img" aria-label="Photo of a sick child in bed with medicine" style="background:linear-gradient(135deg,#d8dde6,#f1ece6 50%,#c9a58a)"></div>
  <div class="abs body"><h4>Common Childhood Illnesses</h4><div class="meta">14 December, 2016, by Admin</div><p>As they grow and develop, children come in contact with and may sometimes suffer from a variety of common illnesses...</p><div class="more">+ MORE</div></div>
</article>
<article class="abs post" style="left:152px;top:1647px">
  <div class="abs thumb" role="img" aria-label="Photo of a pregnant woman resting" style="background:linear-gradient(135deg,#f3f0ee,#d9b49a 50%,#7a8fc4)"></div>
  <div class="abs body"><h4>Now That You Are Pregnant</h4><div class="meta">14 December, 2016, by Admin</div><p>Congratulations on your pregnancy! A pregnancy that is planned is a thing of joy. There are many changes and adjustments...</p><div class="more">+ MORE</div></div>
</article>
<article class="abs post" style="left:620px;top:1647px">
  <div class="abs thumb" role="img" aria-label="Photo of a mother holding her newborn baby" style="background:linear-gradient(135deg,#6d5b50,#e5d3c8 50%,#f4f1ef)"></div>
  <div class="abs body"><h4>Newborn Care</h4><div class="meta">14 December, 2016, by Admin</div><p>Everyone needs adequate nutrition, and so does your baby. The most natural food for babies is breast milk. Newborn baby and...</p><div class="more">+ MORE</div></div>
</article>

<section class="abs health" role="region" aria-label="Sunbrook Health Center">
  <h2>Sunbrook Health Center</h2>
  <div class="tags">
    <span class="tag">Well Child Information</span><span class="tag">Immunizations</span><span class="tag">Newborn Care</span><span class="tag">Now That You Are Pregnant</span>
    <span class="tag">Parenting Resources</span><span class="tag">Common Childhood Illnesses</span>
  </div>
</section>

<section>
  <div class="abs contact-sec"><h2>Contact Us</h2></div>
  <div class="abs about">
    <h3>About Sunbrook Pediatrics</h3>
    <p>At Sunbrook Pediatrics, you will find a pediatrician and an environment that is warm and compassionate. All of our staff members are knowledgeable, caring, efficient, and ready to serve you.</p>
    <p>The general atmosphere is pleasant, flexible and fun-filled for you and your family to enjoy. It is our pleasure to provide you and your children with our wide range of services.</p>
  </div>
  <div class="abs info">
    <h3>Contact Info</h3>
    <ul>
      <li><svg viewBox="0 0 12 12"><path d="M6 0a4 4 0 0 0-4 4c0 3 4 8 4 8s4-5 4-8a4 4 0 0 0-4-4zm0 6a2 2 0 1 1 0-4 2 2 0 0 1 0 4z"/></svg>Sunbrook Pediatrics 15A Alder Park Linwood, GA 30199</li>
      <li><svg viewBox="0 0 12 12"><rect x="3" y="0" width="6" height="12" rx="1"/></svg>(555) 014-2739</li>
      <li><svg viewBox="0 0 12 12"><path d="M0 2h12v8H0zM0 2l6 5 6-5" stroke="#fff" stroke-width=".8"/></svg>info@sunbrookkids.com</li>
    </ul>
  </div>
  <div class="abs social">
    <span class="soc"><i></i>Friendly</span>
    <span class="soc"><i></i>Linkwise</span>
    <span style="width:14px"></span>
    <span class="pay">Monetrix</span><span class="pay">Cardora</span><span class="pay">Orbicard</span><span class="pay">Payvex</span>
  </div>
  <div class="abs map" role="img" aria-label="Vorlund street map showing the office location at Alder Park"></div>
</section>

<footer class="abs footer">
  <nav class="abs">Home &nbsp;|&nbsp; About Us &nbsp;|&nbsp; Our Services &nbsp;|&nbsp; Sunbrook Health Center &nbsp;|&nbsp; Forms &nbsp;|&nbsp; Latest News &nbsp;|&nbsp; Contact Us</nav>
  <div class="abs copy">Copyright © 2017 Company name. All rights reserved.</div>
  <div class="abs flogo"><i></i><span>SUNBROOK<br>PEDIATRICS</span></div>
</footer>
</body>
</html>
```